Realty Group Needs Classy, Contemporary Letterhead Design

We need a letterhead design for a new realty company located in NY, USA. We buy investment properties to rehabilitate and or keep in our rental portfolio.

```html
<!DOCTYPE html>
<html lang="en">
<head>
<meta charset="utf-8">
<title>Halvern Realty Group Letterhead</title>
<link rel="stylesheet" href="https://fonts.googleapis.com/css2?family=Montserrat:wght@800&family=Questrial&display=swap">
<style>
  :root {
    --brand-purple: #4b2a8a;
    --brand-faint: #d6cee5;
    --text-gray: #6a6a6a;
    --page-edge: #d4d4d4;
    --canvas-bg: #ffffff;
  }
  * { margin: 0; padding: 0; box-sizing: border-box; }
  html, body {
    width: 1125px; height: 1200px; overflow: hidden;
    background: var(--canvas-bg);
  }
  .canvas { position: relative; width: 1125px; height: 1200px; }
  .sheet {
    position: absolute; left: 169px; top: 90px;
    width: 787px; height: 1019px;
    background: #fff;
    border: 1px solid var(--page-edge);
    box-shadow: 1px 2px 3px rgba(0,0,0,0.12);
  }
  .brand-name {
    position: absolute; left: 47px; top: 62px;
    font-family: "Montserrat", sans-serif; font-weight: 800;
    font-size: 27px; letter-spacing: -0.3px;
    color: var(--brand-purple); white-space: nowrap;
  }
  .header-rule {
    position: absolute; left: 47px; top: 145px;
    width: 694px; height: 1.5px; background: var(--brand-purple);
  }
  .contact-group {
    position: absolute; top: 72px;
    display: flex; align-items: stretch;
  }
  .contact-group.phones { left: 438px; }
  .contact-group.fax-web { left: 571px; }
  .contact-icons {
    display: flex; flex-direction: column; justify-content: space-between;
    padding: 3px 0; width: 15px;
  }
  .contact-icons svg { width: 12px; height: 12px; fill: var(--brand-purple); }
  .contact-divider { width: 1.5px; background: var(--brand-purple); margin: 0 4px 0 2px; height: 43px; }
  .contact-lines {
    display: flex; flex-direction: column; justify-content: space-between;
    padding: 4px 0 2px;
    font-family: "Questrial", sans-serif; font-size: 10.5px;
    color: var(--text-gray); white-space: nowrap;
  }
  .footer-mark {
    position: absolute; left: 0; right: 0; top: 880px;
    text-align: center;
    font-family: "Montserrat", sans-serif; font-weight: 800;
    font-size: 40px; color: var(--brand-faint);
    white-space: nowrap;
  }
</style>
</head>
<body>
<div class="canvas">
  <div class="sheet">
    <div class="brand-name">Halvern Realty Group, LLC</div>

    <div class="contact-group phones">
      <div class="contact-icons">
        <svg viewBox="0 0 12 12" aria-label="Office phone"><rect x="0" y="0" width="12" height="12" rx="1.5"/><path d="M3.2 2.6l1.3-.3.7 1.7-.8.6c.4.9 1 1.5 1.9 1.9l.6-.8 1.7.7-.3 1.3c-3 .2-5.3-2.1-5.1-5.1z" fill="#fff"/></svg>
        <svg viewBox="0 0 12 12" aria-label="Mobile phone"><path d="M3 1.5h4.5v10H2V1.5zm.8.8v8.4h3V2.3z"/><rect x="7.5" y="0" width="3" height="4"/></svg>
      </div>
      <div class="contact-divider"></div>
      <div class="contact-lines">
        <span>(123) 456-7890</span>
        <span>(123) 456-7890</span>
      </div>
    </div>

    <div class="contact-group fax-web">
      <div class="contact-icons">
        <svg viewBox="0 0 12 12" aria-label="Fax"><rect x="3" y="0.5" width="6" height="3"/><rect x="0.5" y="4" width="11" height="5" rx="1"/><rect x="3" y="7.5" width="6" height="4" fill="#fff" stroke="#4b2a8a" stroke-width="1"/></svg>
        <svg viewBox="0 0 12 12" aria-label="Website"><circle cx="6" cy="6" r="5.5"/><path d="M0.5 6h11M6 .5v11M2 3h8M2 9h8" stroke="#fff" stroke-width="0.8" fill="none"/><ellipse cx="6" cy="6" rx="2.3" ry="5.5" stroke="#fff" stroke-width="0.8" fill="none"/></svg>
      </div>
      <div class="contact-divider"></div>
      <div class="contact-lines">
        <span>(123) 456-789012</span>
        <span>www.halvernrealtygrp.com</span>
      </div>
    </div>

    <div class="header-rule"></div>

    <div class="footer-mark">Halvern Realty Group, LLC</div>
  </div>
</div>
</body>
</html>
```